Brand Identity Stationary Package

Hello I'm looking for a full branding package for my Property Management Company. I have a logo but looking to have the following
Business Card
Email signature
Facebook cover photo
Letterhead (word.doc)
#10 Envelope
Pocket Folder - link to 9x12 pocket folder design specs https://www.printorbit-example.ca/marketing-materials/presentation-folders
would like everything to match and be brand identifiable. The company looks after residential properties/apartments and some commercial properties. Attached is a zip of the files.
For Business Card
Name: Gareth Lindqvist
Position: Operations Manager
Number: 1 (555) 384-2917
Email: Gareth@harborkey-example.ca
Website: Harborkey-example.ca
Property Management

```html
<!DOCTYPE html>
<html lang="en">
<head>
<meta charset="utf-8">
<title>Harborkey Property Management – #10 Envelope</title>
<link rel="stylesheet" href="https://fonts.googleapis.com/css2?family=Montserrat:wght@600&family=Source+Sans+3:wght@400&display=swap">
<style>
  :root {
    --brand-green: #80a642;
    --ink: #111111;
    --paper: #f6f6f6;
    --backdrop: #d4d4d4;
    --flap-white: #f7f7f7;
  }
  * { margin: 0; padding: 0; box-sizing: border-box; }
  html, body {
    width: 1200px;
    height: 1050px;
    overflow: hidden;
    background: var(--backdrop);
  }
  .stationery {
    position: relative;
    width: 1200px;
    height: 1050px;
  }
  .envelope {
    position: absolute;
    left: 145px;
    width: 910px;
    height: 390px;
    display: block;
  }
  .envelope--back { top: 105px; }
  .envelope--front { top: 555px; }
  .paper { fill: var(--paper); }
  .band-green { fill: var(--brand-green); }
  .band-black { fill: var(--ink); }
  .wordmark {
    font-family: "Montserrat", sans-serif;
    font-weight: 600;
    letter-spacing: 4px;
  }
  .wordmark--light { fill: #ffffff; font-size: 38px; }
  .wordmark--dark { fill: var(--ink); font-size: 34px; }
  .tagline {
    font-family: "Montserrat", sans-serif;
    font-weight: 600;
    font-size: 9.5px;
    letter-spacing: 7.4px;
  }
  .tagline--light { fill: #ffffff; }
  .tagline--dark { fill: var(--ink); }
  .contact-line {
    font-family: "Source Sans 3", sans-serif;
    font-size: 20px;
    fill: var(--ink);
  }
  .contact-icon { fill: var(--brand-green); }
</style>
</head>
<body>
<main class="stationery">

  <!-- Envelope back with flap -->
  <svg class="envelope envelope--back" viewBox="0 0 910 390" aria-label="Envelope back">
    <rect class="paper" x="0" y="0" width="910" height="390"/>
    <path class="band-green" d="M0 0 H910 L884 91 Q872 128 833 131 H74 Q36 128 25 91 Z"/>
    <text class="wordmark wordmark--light" x="455" y="69" text-anchor="middle">HARBORKEY</text>
    <text class="tagline tagline--light" x="458" y="88" text-anchor="middle">PROPERTY MANAGEMENT</text>
  </svg>

  <!-- Envelope front with return address -->
  <svg class="envelope envelope--front" viewBox="0 0 910 390" aria-label="Envelope front">
    <rect class="paper" x="0" y="0" width="910" height="390"/>

    <polygon class="band-green" points="0,0 910,0 910,33 306,29 254,62 0,61"/>
    <polygon class="band-black" points="314,38 910,43 910,59 292,54"/>

    <polygon class="band-black" points="0,334 614,338 591,355 0,350"/>
    <polygon class="band-green" points="652,329 910,331 910,390 0,390 0,357 600,362"/>

    <text class="wordmark wordmark--dark" x="52" y="142">HARBORKEY</text>
    <text class="tagline tagline--dark" x="52" y="158">PROPERTY MANAGEMENT</text>

    <g class="contact">
      <g class="contact-icon" transform="translate(52,198)">
        <path d="M0 5 Q8 -1 16 5 L14 8 L11 6 L11 4 Q8 3 5 4 L5 6 L2 8 Z"/>
        <rect x="3" y="8" width="10" height="6" rx="1"/>
      </g>
      <text class="contact-line" x="80" y="214">1 (555) 384-2917</text>

      <g class="contact-icon" transform="translate(52,226)">
        <rect x="0" y="0" width="16" height="11"/>
        <path d="M0 0 L8 6 L16 0" fill="none" stroke="#ffffff" stroke-width="1.4"/>
      </g>
      <text class="contact-line" x="80" y="240">Gareth@harborkey-example.ca</text>

      <g transform="translate(60,258)">
        <circle class="contact-icon" r="8"/>
        <path d="M-5 -3 Q-2 -6 1 -4 L0 0 L-4 1 Z M2 2 L5 1 L4 5 Z" fill="#ffffff"/>
      </g>
      <text class="contact-line" x="80" y="266">www.Harborkey-example.ca</text>
    </g>
  </svg>

</main>
</body>
</html>
```